Website Design - TallyPorchHelpers.net

PLEASE CHECK WORD DOCUMENT ATTACHED FOR WEBSITE FLOW.

Target Market(s)

REAL ESTATE AGENTS ARE THE TARGET MARKET

Industry/Entity Type

Real Estate

Coding

Coded - Design and coding required

Number of Pages Required

4 page

Colors

Designer to choose colors to be used in the design.

Requirements
Must have
• WE LIKE RED LOGO ATTACHED
Nice to have
• PLEASE CHECK WORD DOCUMENT ATTACHED FOR WEBSITE FLOW.
Should not have

```html
<!DOCTYPE html>
<html lang="en">
<head>
<meta charset="utf-8">
<title>Tally Porch Helpers</title>
<link href="https://fonts.googleapis.com/css2?family=Poppins:wght@400;500;600;700&family=Lato:wght@400;700&display=swap" rel="stylesheet">
<style>
:root{
  --red:#e8202a;
  --ink:#2f2f2f;
  --text:#555;
  --blue-a:#2d5ec1;
  --blue-b:#29a2e2;
  --white:#fff;
  --footer:#0b0b0b;
  --line:#ddd;
}
*{box-sizing:border-box;margin:0;padding:0}
html,body{width:1200px;height:2941px;overflow:hidden}
body{font-family:'Lato',sans-serif;color:var(--text);background:var(--white);position:relative}
section,header,footer{position:absolute;left:0;width:1200px}
.abs{position:absolute}
/* header */
.site-header{top:0;height:114px;background:var(--white)}
.brand{left:98px;top:34px;display:flex;align-items:center;gap:10px;font-family:'Poppins',sans-serif;font-weight:700;font-size:22px;color:var(--red);line-height:1}
.brand-mark{width:30px;height:30px;background:var(--red)}
.main-nav{left:260px;top:56px;display:flex;gap:30px;font-family:'Poppins',sans-serif;font-weight:500;font-size:15px;color:var(--ink);text-transform:uppercase}
.call{left:870px;top:30px;font-family:'Poppins',sans-serif;color:var(--ink)}
.call small{display:block;font-size:13px;font-weight:600;margin-bottom:6px}
.call span{display:flex;align-items:center;gap:12px;font-size:21px}
/* hero */
.hero{top:114px;height:533px;background:linear-gradient(180deg,#9c9586 0%,#8a8a80 45%,#4f6d2f 72%,#3e5b22 100%)}
.hero-tagline{left:440px;top:210px;width:662px;text-align:right;font-family:'Poppins',sans-serif;font-weight:600;font-size:26px;line-height:42px;color:var(--white)}
.hero-pager{left:540px;top:478px;display:flex;align-items:center;gap:14px;color:var(--white);font-family:'Poppins',sans-serif;font-size:14px}
/* choose */
.choose{top:647px;height:453px;text-align:center}
.section-title{font-family:'Poppins',sans-serif;font-weight:600;font-size:32px;line-height:45px;color:var(--ink);text-transform:uppercase}
.choose .section-title{position:absolute;top:82px;left:0;width:1200px}
.choose-intro{position:absolute;top:200px;left:160px;width:880px;font-size:14.5px;line-height:27px}
.option-row{position:absolute;top:292px;left:261px;display:flex;gap:71px}
.option{width:170px;height:61px;border:2px solid var(--red);border-radius:6px;color:var(--red);font-family:'Poppins',sans-serif;font-weight:500;font-size:14px;line-height:19px;display:flex;align-items:center;justify-content:center;text-transform:uppercase;background:var(--white)}
.option.is-active{background:var(--red);color:var(--white)}
/* pricing */
.pricing{top:1100px;height:735px;background:linear-gradient(120deg,var(--blue-a),var(--blue-b))}
.pricing .section-title{position:absolute;top:80px;width:1200px;text-align:center;color:var(--white)}
.pricing-intro{position:absolute;top:128px;left:280px;width:640px;text-align:center;color:var(--white);font-size:15px;line-height:26px}
.plan{position:absolute;background:var(--white);text-align:center}
.plan h3{font-family:'Poppins',sans-serif;font-weight:600;font-size:30px;color:var(--ink);line-height:1}
.plan .plan-sub{font-size:13px;color:var(--ink);margin-top:6px}
.plan ul{list-style:none;text-align:justify;margin:26px 22px 0;border-top:1px solid #999;padding-top:20px}
.plan li{position:relative;padding-left:22px;font-size:11.5px;line-height:22px;color:var(--ink);margin-bottom:8px}
.plan li svg{position:absolute;left:0;top:6px}
.buy{display:inline-block;border:2px solid var(--red);color:var(--red);font-family:'Poppins',sans-serif;font-weight:600;font-size:13px;padding:8px 14px;border-radius:4px;margin-top:12px}
.plan-side{top:227px;width:241px;height:381px;padding-top:34px}
.plan-left{left:206px}
.plan-right{left:755px}
.plan-main{left:447px;top:206px;width:304px;height:423px;border:3px solid #111;z-index:2}
.plan-main .plan-head{background:var(--red);height:66px;margin-top:26px;padding-top:10px;color:var(--white)}
.plan-main h3{color:var(--white);font-size:32px}
.plan-main .plan-sub{color:var(--white);margin-top:2px}
.plan-main ul{border-top:none;margin-top:10px}
.plan-main .buy{background:var(--red);color:var(--white);font-size:15px;padding:10px 18px;border-radius:8px}
.slide-arrow{top:346px}
/* services */
.services{top:1835px;height:757px;text-align:center}
.services .section-title{position:absolute;top:118px;width:1200px}
.service{position:absolute;top:240px;width:250px;margin-left:-125px}
.service .ring{width:144px;height:144px;border:1.5px solid #bbb;border-radius:50%;margin:0 auto;display:flex;align-items:center;justify-content:center}
.service h4{font-family:'Poppins',sans-serif;font-weight:500;font-size:22px;color:var(--ink);margin-top:22px}
.service p{font-size:14px;line-height:25.5px;color:var(--text);margin-top:6px;padding:0 12px}
.subscribe{position:absolute;top:598px;left:318px;width:539px;height:57px;border:1.5px solid #888;border-radius:10px;overflow:hidden;display:flex}
.subscribe span{flex:1;padding-left:38px;line-height:54px;text-align:left;font-size:14.5px;color:var(--ink)}
.subscribe b{width:187px;background:var(--red);color:var(--white);font-family:'Poppins',sans-serif;font-weight:600;font-size:17px;line-height:54px;text-transform:uppercase}
/* footer */
.site-footer{top:2592px;height:349px;background:var(--footer);color:var(--white)}
.foot-col{position:absolute;top:70px}
.foot-col h5{font-family:'Poppins',sans-serif;font-weight:600;font-size:15px;text-transform:uppercase;margin-bottom:10px}
.foot-col li{list-style:none;font-size:12.5px;line-height:27.5px;display:flex;gap:8px;align-items:flex-start}
.foot-col li.multi{line-height:25px}
.foot-col .chev{font-size:12px}
.social{display:flex;gap:12px;margin-top:4px}
.social i{display:block;width:12px;height:12px;border-radius:50%;background:var(--white)}
.foot-rule{position:absolute;top:290px;left:98px;width:1004px;height:1px;background:#555}
.copyright{position:absolute;top:313px;width:1200px;text-align:center;font-size:12.5px}
</style>
</head>
<body>

<header class="site-header">
  <div class="abs brand"><span class="brand-mark"></span>Tally Porch Helpers</div>
  <nav class="abs main-nav"><span>Home</span><span>How it works</span><span>Service area</span><span>Pricing</span><span>About us</span><span>FAQ</span></nav>
  <div class="abs call"><small>CALL US ON</small><span>
    <svg width="26" height="26" viewBox="0 0 24 24"><path d="M6.6 10.8c1.4 2.8 3.8 5.1 6.6 6.6l2.2-2.2c.3-.3.7-.4 1-.2 1.1.4 2.3.6 3.6.6.6 0 1 .4 1 1V20c0 .6-.4 1-1 1C10.6 21 3 13.4 3 4c0-.6.4-1 1-1h3.5c.6 0 1 .4 1 1 0 1.3.2 2.5.6 3.6.1.3 0 .7-.2 1L6.6 10.8z" fill="#222"/></svg>
    (+1) 555-010-2040</span></div>
</header>

<section class="hero" role="img" aria-label="Photo of an open house yard sign on a front lawn before a suburban home">
  <p class="abs hero-tagline">Helping agents save time and money. We place signs and boost foot traffic to your open houses using proven marketing techniques.</p>
  <div class="abs hero-pager">
    <svg width="20" height="10" viewBox="0 0 20 10"><path d="M19 5H2M6 1L2 5l4 4" stroke="#fff" stroke-width="2" fill="none"/></svg>
    <span>1 of 4</span>
    <svg width="20" height="10" viewBox="0 0 20 10"><path d="M1 5h17M14 1l4 4-4 4" stroke="#fff" stroke-width="2" fill="none"/></svg>
  </div>
</section>

<section class="choose">
  <h2 class="section-title">Choose the option below that<br>best describes you</h2>
  <p class="choose-intro">Lorem ipsum dolor sit amet, consectetur adipiscing elit, sed do eiusmod tempor incididunt ut labore et dolore magna aliqua. Ut enim ad minim veniam, quis nostrud exercitation ullamco laboris nisi irure dolor in reprehenderit in vatur.</p>
  <div class="option-row">
    <div class="option">I'm a full<br>on brokerage</div>
    <div class="option is-active">I'm an ind.<br>broker with a team</div>
    <div class="option">I need sign<br>placement ASAP</div>
  </div>
</section>

<section class="pricing">
  <h2 class="section-title">Pricing</h2>
  <p class="pricing-intro">Lorem Ipsum is simply dummy text of the printing and typesetting industry. Lorem Ipsums has been the industry's standard dummy text ever since the 1500.</p>

  <svg class="abs slide-arrow" style="left:58px" width="14" height="20" viewBox="0 0 14 20"><path d="M11 2L3 10l8 8" stroke="#cfe0f7" stroke-width="2" fill="none"/></svg>
  <svg class="abs slide-arrow" style="left:1122px" width="14" height="20" viewBox="0 0 14 20"><path d="M3 2l8 8-8 8" stroke="#cfe0f7" stroke-width="2" fill="none"/></svg>

  <div class="plan plan-side plan-left">
    <h3>5 SIGNS</h3><p class="plan-sub">Lorem Ipsum</p>
    <ul>
      <li><svg width="11" height="9" viewBox="0 0 11 9"><path d="M1 4.5l3 3L10 1" stroke="#222" stroke-width="2" fill="none"/></svg>Place signs strategically in best areas according to where the open house is located</li>
      <li><svg width="11" height="9" viewBox="0 0 11 9"><path d="M1 4.5l3 3L10 1" stroke="#222" stroke-width="2" fill="none"/></svg>Pick Up the signs after the open house</li>
      <li><svg width="11" height="9" viewBox="0 0 11 9"><path d="M1 4.5l3 3L10 1" stroke="#222" stroke-width="2" fill="none"/></svg>Store custom signs for you if needed</li>
    </ul>
    <span class="buy">BUY NOW</span>
  </div>

  <div class="plan plan-main">
    <div class="plan-head"><h3>10 SIGNS</h3><p class="plan-sub">Lorem Ipsum</p></div>
    <ul>
      <li><svg width="11" height="9" viewBox="0 0 11 9"><path d="M1 4.5l3 3L10 1" stroke="#e8202a" stroke-width="2" fill="none"/></svg>Place signs strategically in best areas according to where the open house is located</li>
      <li><svg width="11" height="9" viewBox="0 0 11 9"><path d="M1 4.5l3 3L10 1" stroke="#e8202a" stroke-width="2" fill="none"/></svg>Pick Up the signs after the open house</li>
      <li><svg width="11" height="9" viewBox="0 0 11 9"><path d="M1 4.5l3 3L10 1" stroke="#e8202a" stroke-width="2" fill="none"/></svg>Store custom signs for you if needed</li>
    </ul>
    <span class="buy">BUY NOW</span>
  </div>

  <div class="plan plan-side plan-right">
    <h3>15 SIGNS</h3><p class="plan-sub">Lorem Ipsum</p>
    <ul>
      <li><svg width="11" height="9" viewBox="0 0 11 9"><path d="M1 4.5l3 3L10 1" stroke="#222" stroke-width="2" fill="none"/></svg>Place signs strategically in best areas according to where the open house is located</li>
      <li><svg width="11" height="9" viewBox="0 0 11 9"><path d="M1 4.5l3 3L10 1" stroke="#222" stroke-width="2" fill="none"/></svg>Pick Up the signs after the open house</li>
      <li><svg width="11" height="9" viewBox="0 0 11 9"><path d="M1 4.5l3 3L10 1" stroke="#222" stroke-width="2" fill="none"/></svg>Store custom signs for you if needed</li>
    </ul>
    <span class="buy">BUY NOW</span>
  </div>
</section>

<section class="services">
  <h2 class="section-title">Sign up for a subscription and get these<br>marketing services for free</h2>

  <div class="service" style="left:198px">
    <div class="ring"><svg width="66" height="62" viewBox="0 0 66 62"><path d="M6 4h54a3 3 0 0 1 3 3v32a3 3 0 0 1-3 3H30l-12 14V42H6a3 3 0 0 1-3-3V7a3 3 0 0 1 3-3z" fill="none" stroke="#e8202a" stroke-width="3.5"/><text x="33" y="29" text-anchor="middle" font-family="Poppins, sans-serif" font-size="16" font-weight="600" fill="#e8202a">sms</text></svg></div>
    <h4>SMS</h4>
    <p>Send sms blast to your neighborhood informing them your home is for sale and if they know anyone looking to send them over</p>
  </div>

  <div class="service" style="left:463px">
    <div class="ring"><svg width="80" height="54" viewBox="0 0 80 54"><rect x="2" y="2" width="76" height="50" fill="none" stroke="#e8202a" stroke-width="3.5"/><path d="M2 2l38 30L78 2M2 52l28-24M78 52L50 28" fill="none" stroke="#e8202a" stroke-width="3.5"/></svg></div>
    <h4>EMAIL</h4>
    <p>Email blast to your neighborhood informing them your home is for sale and if they know anyone looking to send them over</p>
  </div>

  <div class="service" style="left:727px">
    <div class="ring"><svg width="48" height="48" viewBox="0 0 48 48"><rect x="2" y="2" width="44" height="44" fill="#e8202a"/></svg></div>
    <h4>FB AD</h4>
    <p>Newsfeed ads to people in your open house area</p>
  </div>

  <div class="service" style="left:994px">
    <div class="ring"><svg width="48" height="48" viewBox="0 0 48 48"><circle cx="24" cy="24" r="22" fill="#e8202a"/></svg></div>
    <h4>VB</h4>
    <p>VB blast to your neighborhood informing them your home is for sale and if they know anyone looking to send them over</p>
  </div>

  <div class="subscribe"><span>Enter Your Email Address</span><b>Subscribe</b></div>
</section>

<footer class="site-footer">
  <div class="foot-col" style="left:98px">
    <h5>Quick Links</h5>
    <ul>
      <li><span class="chev">»</span>Home</li><li><span class="chev">»</span>How It Works</li><li><span class="chev">»</span>Service Areas</li><li><span class="chev">»</span>Pricing</li><li><span class="chev">»</span>About Us</li><li><span class="chev">»</span>FAQ</li>
    </ul>
  </div>
  <div class="foot-col" style="left:282px">
    <h5>Contact</h5>
    <ul>
      <li class="multi"><svg width="10" height="14" viewBox="0 0 10 14" style="margin-top:6px"><path d="M5 0a5 5 0 0 1 5 5c0 4-5 9-5 9S0 9 0 5a5 5 0 0 1 5-5z" fill="#fff"/><circle cx="5" cy="5" r="1.8" fill="#0b0b0b"/></svg><span>Tally Porch Helpers,<br>1619 S. Lorem Ipsum Is Simple,<br>Lorem Ipsum.</span></li>
      <li><svg width="12" height="12" viewBox="0 0 24 24" style="margin-top:8px"><path d="M6.6 10.8c1.4 2.8 3.8 5.1 6.6 6.6l2.2-2.2c.3-.3.7-.4 1-.2 1.1.4 2.3.6 3.6.6.6 0 1 .4 1 1V20c0 .6-.4 1-1 1C10.6 21 3 13.4 3 4c0-.6.4-1 1-1h3.5c.6 0 1 .4 1 1 0 1.3.2 2.5.6 3.6.1.3 0 .7-.2 1L6.6 10.8z" fill="#fff"/></svg>(+1) 555-010-2040</li>
      <li><svg width="12" height="10" viewBox="0 0 12 10" style="margin-top:9px"><rect width="12" height="10" fill="#fff"/><path d="M0 0l6 5 6-5" stroke="#0b0b0b" fill="none"/></svg>info@tallyporchhelpers.net</li>
    </ul>
  </div>
  <div class="foot-col" style="left:555px">
    <h5>Other Links</h5>
    <ul><li><span class="chev">»</span>Latest Work</li><li><span class="chev">»</span>Blog</li><li><span class="chev">»</span>Contact Us</li></ul>
  </div>
  <div class="foot-col" style="left:729px;width:200px">
    <h5>Recent Tweets</h5>
    <ul>
      <li class="multi"><i style="display:block;flex:none;width:10px;height:10px;border-radius:50%;background:#fff;margin-top:7px"></i><span>Sed ut perspiciatis ude omnis iste natus.</span></li>
      <li class="multi" style="margin-top:12px"><i style="display:block;flex:none;width:10px;height:10px;border-radius:50%;background:#fff;margin-top:7px"></i><span>There are many variations of passages of Lorem Ipsum.</span></li>
    </ul>
  </div>
  <div class="foot-col" style="left:984px">
    <h5>Follow Us On</h5>
    <div class="social"><i></i><i></i><i></i></div>
  </div>
  <div class="foot-rule"></div>
  <p class="copyright">Copyrights © 2018 . All Rights Reserved.</p>
</footer>

</body>
</html>
```